Website Design - TallyPorchHelpers.net

PLEASE CHECK WORD DOCUMENT ATTACHED FOR WEBSITE FLOW.

Target Market(s)

REAL ESTATE AGENTS ARE THE TARGET MARKET

Industry/Entity Type

Real Estate

Coding

Coded - Design and coding required

Number of Pages Required

4 page

Colors

Designer to choose colors to be used in the design.

Requirements
Must have
• WE LIKE RED LOGO ATTACHED
Nice to have
• PLEASE CHECK WORD DOCUMENT ATTACHED FOR WEBSITE FLOW.
Should not have

```html
<!DOCTYPE html>
<html lang="en">
<head>
<meta charset="utf-8">
<title>Tally Porch Helpers</title>
<link rel="stylesheet" href="https://fonts.googleapis.com/css2?family=Montserrat:wght@400;600;700;800&family=Open+Sans:wght@400;600&display=swap">
<style>
:root{
  --navy:#221b80;
  --navy-deep:#1d1878;
  --red:#e3121c;
  --ink:#141414;
  --grey-text:#444;
  --mist:#f1eeef;
  --pale:#f3f3f3;
  --white:#fff;
  --charcoal:#3f3f3f;
  --hero-a:#c9cfd3;
  --hero-b:#a7ad9c;
}
*{box-sizing:border-box;margin:0;padding:0}
html,body{width:1200px;height:3422px;overflow:hidden}
body{position:relative;font-family:"Open Sans",Arial,sans-serif;color:var(--ink);background:var(--white)}
.abs{position:absolute}

/* hero */
.hero{left:0;top:0;width:1200px;height:677px;background:linear-gradient(160deg,var(--hero-a) 0%,var(--hero-b) 100%)}
.brand{left:137px;top:30px;font-family:"Montserrat",sans-serif;font-weight:800;color:var(--navy);font-size:27px;line-height:27px;display:flex;align-items:center;gap:12px}
.brand .mark{width:44px;height:44px;background:var(--navy)}
.call{left:866px;top:26px;display:flex;gap:10px;align-items:center;color:var(--navy)}
.call small{display:block;font-family:"Montserrat",sans-serif;font-weight:700;font-size:12px}
.call strong{font-family:"Montserrat",sans-serif;font-weight:800;font-size:24px;line-height:26px}
.nav{left:565px;top:84px;display:flex;gap:34px;font-family:"Montserrat",sans-serif;font-weight:700;font-size:15px;color:var(--ink)}
.hero-title{left:755px;top:206px;font-family:"Montserrat",sans-serif;font-weight:700;font-size:31px;color:var(--ink)}
.btn-red{background:var(--red);color:var(--white);font-family:"Montserrat",sans-serif;font-weight:700;font-size:13px;display:flex;align-items:center;justify-content:center;border-radius:3px}
.hero-more{left:760px;top:258px;width:102px;height:30px}
.dots{left:556px;top:602px;display:flex;gap:12px;align-items:center}
.dots span{width:9px;height:9px;border-radius:50%;background:var(--white)}
.dots .on{width:14px;height:14px;border:2px solid var(--navy);background:var(--white)}

/* mission */
.mission{left:0;top:677px;width:1200px;height:354px;background:var(--mist)}
.mission-art{left:194px;top:65px;width:286px;height:289px;background:linear-gradient(180deg,#e4e1e2,#d9d6d7)}
.mission h2{position:absolute;left:563px;top:118px;font-family:"Montserrat",sans-serif;font-weight:700;font-size:23px}
.mission p{position:absolute;left:563px;top:174px;width:470px;font-size:17px;line-height:26px;color:var(--grey-text)}

/* choose */
.choose{left:0;top:1031px;width:1200px;height:376px;background:var(--white);text-align:center}
.two-line{font-family:"Montserrat",sans-serif;font-size:25px;line-height:38px;color:var(--ink)}
.two-line b{font-weight:700;display:block}
.choose .two-line{position:absolute;left:0;width:1200px;top:86px}
.choice{top:219px;height:52px;color:var(--white);font-family:"Montserrat",sans-serif;font-weight:700;font-size:14px;display:flex;align-items:center;justify-content:center;border-radius:3px}
.choice.navy{left:187px;width:235px;background:var(--navy)}
.choice.dark{left:438px;width:287px;background:var(--charcoal)}
.choice.red{left:737px;width:287px;background:var(--red)}

/* packages */
.packages{left:0;top:1407px;width:1200px;height:913px;background:var(--pale)}
.packages h2{position:absolute;top:66px;width:1200px;text-align:center;font-family:"Montserrat",sans-serif;font-weight:700;font-size:24px}
.packages .rule{position:absolute;left:582px;top:112px;width:36px;height:3px;background:#c9c9c9}
.pack{width:310px;height:354px}
.pack svg{position:absolute;left:0;top:0;filter:drop-shadow(0 2px 8px rgba(0,0,0,.12))}
.pack-body{position:absolute;left:32px;top:50px;width:246px;text-align:center}
.pack-name{font-family:"Montserrat",sans-serif;font-weight:700;font-size:17px}
.pack-price{font-family:"Montserrat",sans-serif;font-weight:700;font-size:28px;color:var(--red);margin-top:4px}
.pack ul{list-style:none;text-align:left;margin-top:14px}
.pack li{font-size:11.5px;line-height:14px;padding:8px 0 8px 24px;position:relative;border-bottom:1px solid #e5e5e5;white-space:normal}
.pack li:last-child{border-bottom:0}
.pack li::before{content:"»";position:absolute;left:4px;top:6px;font-size:15px;font-weight:700}
.buy{display:inline-flex;align-items:center;justify-content:center;width:88px;height:28px;background:var(--navy);color:var(--white);font-family:"Montserrat",sans-serif;font-weight:700;font-size:12px;border-radius:3px;margin-top:6px}

/* subscription */
.subscribe{left:0;top:2320px;width:1200px;height:668px;background:var(--white)}
.subscribe .two-line{position:absolute;left:0;top:100px;width:1200px;text-align:center}
.service{top:246px;width:210px;height:263px;background:var(--white);box-shadow:0 3px 14px rgba(0,0,0,.12);text-align:center;padding-top:30px}
.service .icon{height:60px;display:flex;justify-content:center;align-items:center}
.service h3{font-family:"Montserrat",sans-serif;font-weight:700;font-size:17px;margin-top:18px}
.service p{font-size:12px;line-height:15px;color:#333;width:160px;margin:16px auto 0}
.signup{left:550px;top:579px;width:100px;height:37px;background:var(--navy);color:var(--white);font-family:"Montserrat",sans-serif;font-weight:700;font-size:14px;display:flex;align-items:center;justify-content:center;border-radius:3px}

/* footer */
.footer-band{left:0;top:2988px;width:1200px;height:434px}
.foot-brand{left:137px;top:3142px;font-family:"Montserrat",sans-serif;font-weight:800;font-size:27px;line-height:28px;color:var(--white);display:flex;align-items:center;gap:14px}
.foot-brand .mark{width:50px;height:50px;background:var(--white)}
.foot-col{top:3106px;color:var(--white);font-size:12px}
.foot-col h4{font-family:"Montserrat",sans-serif;font-weight:700;font-size:13px;margin-bottom:22px}
.contact{left:474px}
.contact .row{display:flex;gap:16px;margin-bottom:18px;line-height:17px}
.contact svg{flex:none;margin-top:2px}
.menu{left:760px}
.menu a{display:block;color:var(--white);text-decoration:none;line-height:16px}
.social{left:935px}
.social .row{display:flex;align-items:center;gap:14px;margin-bottom:10px}
.social .dot{width:28px;height:28px;border-radius:50%;background:#2d6fd1}
.social .dot.sky{background:#1da1f2}
.social .dot.dk{background:#12114a}
.foot-rule{left:137px;top:3330px;width:926px;height:1px;background:rgba(255,255,255,.18)}
.copy{left:0;top:3362px;width:1200px;text-align:center;color:var(--white);font-size:12px}
</style>
</head>
<body>

<section class="abs hero" role="img" aria-label="Photo of a two-storey suburban house with landscaped garden and an open house sign on a post"></section>
<div class="abs brand"><span class="mark"></span><span>TALLY PORCH<br>HELPERS</span></div>
<div class="abs call">
  <svg width="34" height="34" viewBox="0 0 24 24"><path fill="#221b80" d="M6.6 10.8a15 15 0 0 0 6.6 6.6l2.2-2.2a1 1 0 0 1 1-.25 11.4 11.4 0 0 0 3.6.57 1 1 0 0 1 1 1V20a1 1 0 0 1-1 1A17 17 0 0 1 3 4a1 1 0 0 1 1-1h3.5a1 1 0 0 1 1 1c0 1.25.2 2.45.57 3.57a1 1 0 0 1-.25 1z"/></svg>
  <div><small>CALL US</small><strong>555.014.2290</strong></div>
</div>
<nav class="abs nav"><span>HOW IT WORKS</span><span>SERVICES</span><span>PRICING</span><span>ABOUT US</span><span>FAQ</span></nav>
<h1 class="abs hero-title">OPEN HOUSE SIGNS</h1>
<div class="abs btn-red hero-more">READ MORE</div>
<div class="abs dots"><span></span><span></span><span class="on"></span><span></span><span></span></div>

<section class="abs mission">
  <div class="abs mission-art" role="img" aria-label="Illustration of a sign post holding a red open house sign"></div>
  <h2>MISSION</h2>
  <p>Helping agents save time and money. We place signs and boost foot traffic to your open houses using proven marketing techniques.</p>
</section>

<section class="abs choose">
  <div class="two-line">CHOOSE THE OPTION BELOW<b>THAT BEST DESCRIBES YOU</b></div>
  <div class="abs choice navy">I'M A FULL ON BROKERAGE</div>
  <div class="abs choice dark">I'M AN IND. BROKER WITH A TEAM</div>
  <div class="abs choice red">I NEED SIGN PLACEMENT ASAP</div>
</section>

<section class="abs packages">
  <h2>PACKAGES</h2>
  <div class="rule"></div>
</section>

<div class="abs pack" style="left:116px;top:1597px">
  <svg width="310" height="354"><polygon points="155,0 310,88 310,266 155,354 0,266 0,88" fill="#fff"/></svg>
  <div class="pack-body"><div class="pack-name">5 SIGNS</div><div class="pack-price">$19.99</div>
  <ul><li>Place signs strategically in best areas according to where the open house is located</li><li>Pick Up the signs after the open house</li><li>Store custom signs for you if needed.</li></ul><span class="buy">BUY NOW</span></div>
</div>
<div class="abs pack" style="left:445px;top:1597px">
  <svg width="310" height="354"><polygon points="155,0 310,88 310,266 155,354 0,266 0,88" fill="#fff"/></svg>
  <div class="pack-body"><div class="pack-name">10 SIGNS</div><div class="pack-price">$21.99</div>
  <ul><li>Place signs strategically in best areas according to where the open house is located</li><li>Pick Up the signs after the open house</li><li>Store custom signs for you if needed.</li></ul><span class="buy">BUY NOW</span></div>
</div>
<div class="abs pack" style="left:773px;top:1597px">
  <svg width="310" height="354"><polygon points="155,0 310,88 310,266 155,354 0,266 0,88" fill="#fff"/></svg>
  <div class="pack-body"><div class="pack-name">15 SIGNS</div><div class="pack-price">$25.99</div>
  <ul><li>Place signs strategically in best areas according to where the open house is located</li><li>Pick Up the signs after the open house</li><li>Store custom signs for you if needed.</li></ul><span class="buy">BUY NOW</span></div>
</div>
<div class="abs pack" style="left:281px;top:1889px">
  <svg width="310" height="354"><polygon points="155,0 310,88 310,266 155,354 0,266 0,88" fill="#fff"/></svg>
  <div class="pack-body"><div class="pack-name">20 SIGNS</div><div class="pack-price">$35.99</div>
  <ul><li>Place signs strategically in best areas according to where the open house is located</li><li>Pick Up the signs after the open house</li><li>Store custom signs for you if needed.</li></ul><span class="buy">BUY NOW</span></div>
</div>
<div class="abs pack" style="left:609px;top:1889px">
  <svg width="310" height="354"><polygon points="155,0 310,88 310,266 155,354 0,266 0,88" fill="#fff"/></svg>
  <div class="pack-body"><div class="pack-name">25 SIGNS</div><div class="pack-price">$45.99</div>
  <ul><li>Place signs strategically in best areas according to where the open house is located</li><li>Pick Up the signs after the open house</li><li>Store custom signs for you if needed.</li></ul><span class="buy">BUY NOW</span></div>
</div>

<section class="abs subscribe">
  <div class="two-line">SIGN UP FOR A SUBSCRIPTION AND<b>GET THESE MARKETING SERVICES FOR FREE</b></div>
  <div class="abs service" style="left:130px">
    <div class="icon"><svg width="50" height="58" viewBox="0 0 50 58"><rect x="6" y="10" width="28" height="46" rx="4" fill="none" stroke="#221b80" stroke-width="4"/><circle cx="20" cy="49" r="2.5" fill="#221b80"/><ellipse cx="36" cy="14" rx="13" ry="10" fill="#221b80"/></svg></div>
    <h3>SMS</h3><p>Send sms blast to your neighborhood informing them your home is for sale and if they know anyone looking to send them over</p>
  </div>
  <div class="abs service" style="left:370px">
    <div class="icon"><svg width="54" height="44" viewBox="0 0 54 44"><rect x="2" y="2" width="50" height="40" fill="#221b80"/><path d="M2 2 27 24 52 2M2 42 21 19M52 42 33 19" fill="none" stroke="#fff" stroke-width="3"/></svg></div>
    <h3>EMAIL</h3><p>E-mail blast to your neighborhood informing them your home is for sale and if they know anyone looking to send them over</p>
  </div>
  <div class="abs service" style="left:609px">
    <div class="icon"><svg width="44" height="44" viewBox="0 0 44 44"><rect x="4" y="4" width="36" height="36" rx="4" fill="#221b80"/></svg></div>
    <h3>FEED AD</h3><p>Newsfeed ads to people in your open house area</p>
  </div>
  <div class="abs service" style="left:853px">
    <div class="icon"><svg width="54" height="54" viewBox="0 0 54 54"><rect x="4" y="4" width="46" height="46" rx="3" fill="#221b80"/></svg></div>
    <h3>VB</h3><p>VB blast to your neighborhood informing them your home is for sale and if they know anyone looking to send them over</p>
  </div>
  <div class="abs signup">SIGNUP</div>
</section>

<svg class="abs footer-band" width="1200" height="434" viewBox="0 0 1200 434">
  <polygon points="0,0 600,50 1200,0 1200,434 0,434" fill="#e3121c"/>
  <polygon points="0,14 600,58 1200,14 1200,434 0,434" fill="#1d1878"/>
</svg>
<div class="abs foot-brand"><span class="mark"></span><span>TALLY PORCH<br>HELPERS</span></div>
<div class="abs foot-col contact">
  <h4>CONTACT US</h4>
  <div class="row"><svg width="10" height="14" viewBox="0 0 10 14"><path d="M5 0a5 5 0 0 1 5 5c0 4-5 9-5 9S0 9 0 5a5 5 0 0 1 5-5z" fill="#fff"/><circle cx="5" cy="5" r="2" fill="#1d1878"/></svg><span>17 Larkspur Lane<br>Brookvale, IL 60077</span></div>
  <div class="row"><svg width="12" height="12" viewBox="0 0 24 24"><path fill="#fff" d="M6.6 10.8a15 15 0 0 0 6.6 6.6l2.2-2.2a1 1 0 0 1 1-.25 11.4 11.4 0 0 0 3.6.57 1 1 0 0 1 1 1V20a1 1 0 0 1-1 1A17 17 0 0 1 3 4a1 1 0 0 1 1-1h3.5a1 1 0 0 1 1 1c0 1.25.2 2.45.57 3.57a1 1 0 0 1-.25 1z"/></svg><span>555.014.2290</span></div>
  <div class="row"><svg width="13" height="10" viewBox="0 0 13 10"><rect width="13" height="10" fill="#fff"/><path d="M0 0 6.5 5.5 13 0" fill="none" stroke="#1d1878" stroke-width="1.3"/></svg><span>info@tallyporchhelpers.net</span></div>
</div>
<div class="abs foot-col menu">
  <h4>MENU</h4>
  <a>Home</a><a>How it works</a><a>Services</a><a>Pricing</a><a>About us</a><a>Faq</a>
</div>
<div class="abs foot-col social">
  <h4>CONNECT WITH US</h4>
  <div class="row"><span class="dot"></span>Friendwall</div>
  <div class="row"><span class="dot sky"></span>Chirpline</div>
  <div class="row"><span class="dot dk"></span>Linkwork</div>
</div>
<div class="abs foot-rule"></div>
<div class="abs copy">Copyrights @ 2018 All Rights Reserved</div>

</body>
</html>
```